Updated website design needed for Radiology Group, Pine Hollow Imaging Partners

Clean, uncluttered, updated design needed for top regional Radiology Center. Focus on personal, patient oriented design, (not clinical). Should be simple and easy to navigate, with clear CTAs. Use blues, greens and photos of people in the Central Oregon outdoors.
Uncoded, PSD design only. 2 pages: Home page and one example interior page.
reference current site: http://www.phipclinic-example.com/
Sites they like:
http://www.valescanlabs-example.com/
http://www.tbmx-example.net/handler.cfm?event=practice,main
http://www.kestrelbonecare-example.com/

Medical Imaging

2 page

Sans Serif

• Personal and patient friendly.
• Lots of white space, clean and uncluttered. Clear CTAs, such as: Patient Bill Pay, Make an Appointment, Meet Our Doctors
• Use copy and contact information from the current site.
• Use outdoor images from Central Oregon, late Winter/ Spring (snow, light colors, spring green, for example)
• Include one example interior page, either Your Exam or Meet Our Doctors
• The client likes:
• Meet Our Doctors slider section, and big, easy to navigate Information Center on www.kestrelbonecare-example.com
• The personal feel of the Your Exam section on www.valescanlabs-example.com
• Blues and Greens, outdoorsy imagery
• The client does not like:
• complex drop down menus
• clinical feel
• Do not use lorum ipsum or dummy text.
• Do not use outdoor images from other regions. Do not use Summer (hot, poolside) or Fall (red/orange leaves) images.

```html
<!DOCTYPE html>
<html lang="en">
<head>
<meta charset="utf-8">
<title>Pine Hollow Imaging Partners</title>
<link href="https://fonts.googleapis.com/css2?family=Ubuntu:wght@300;400;500;700&family=Open+Sans:wght@400;600;700&display=swap" rel="stylesheet">
<style>
:root{
  --blue:#0a86c6;
  --blue-dark:#0872aa;
  --navy:#4a5a9a;
  --green:#3f9a1d;
  --green-light:#5cb82e;
  --ink:#333;
  --muted:#7a7a7a;
  --pale:#eef0f4;
  --foot:#414141;
  --foot-dark:#353535;
  --foot-text:#bdbdbd;
}
*{margin:0;padding:0;box-sizing:border-box}
html,body{width:1200px;height:2740px;overflow:hidden}
body{position:relative;background:#fff;font-family:"Open Sans",Arial,sans-serif;color:var(--ink)}

/* header */
.site-header{position:absolute;left:0;top:0;width:1200px;height:93px;background:linear-gradient(#fff,#eef0f6)}
.brand{position:absolute;left:131px;top:15px;display:flex;align-items:center;gap:12px}
.brand-mark{width:60px;height:62px;background:#7d86bf}
.brand-name{font-family:"Ubuntu",sans-serif;font-size:19px;line-height:22px;color:#3b3f6e;width:170px}
.top-links{position:absolute;right:130px;top:13px;font-size:13px;color:#444}
.top-links span{margin:0 10px}
.call{position:absolute;right:130px;top:46px;font-family:"Ubuntu",sans-serif;font-size:23px;color:#333}
.call b{color:var(--green);font-weight:500}
.main-nav{position:absolute;left:0;top:93px;width:1200px;height:48px;background:var(--blue)}
.main-nav ul{list-style:none;display:flex;position:absolute;left:131px;top:0;height:48px}
.main-nav li{color:#fff;font-size:13px;line-height:48px;padding:0 22px}
.main-nav li.active{background:var(--blue-dark)}

/* hero */
.hero{position:absolute;left:0;top:141px;width:1200px;height:462px;background:linear-gradient(100deg,#52652c 0%,#8a9a52 35%,#c5cfa0 55%,#6d7e3f 80%,#3f5022 100%)}
.hero-caption{position:absolute;left:131px;top:396px;width:426px;height:114px;background:rgba(40,40,70,.78);padding:14px 25px}
.hero-caption h1{font-family:"Ubuntu",sans-serif;font-weight:400;font-size:37px;color:#fff;line-height:46px}
.hero-caption p{font-family:"Ubuntu",sans-serif;font-size:19px;color:#fff;margin-top:2px}
.btn{position:absolute;background:var(--green);color:#fff;font-weight:700;font-size:13px;text-align:center;border-bottom:3px solid #2f7a12}
.hero-btn{left:155px;top:502px;width:207px;height:40px;line-height:38px;font-size:14px}

/* welcome */
.section-title{position:absolute;left:0;width:1200px;text-align:center;font-family:"Ubuntu",sans-serif;font-weight:400;font-size:25px;color:#333}
.section-title span{color:var(--navy)}
.section-sub{position:absolute;left:0;width:1200px;text-align:center;font-size:12.5px;color:var(--muted)}
.welcome-text{position:absolute;left:135px;top:684px;width:930px;text-align:center;font-size:12.5px;line-height:27px;color:var(--muted)}
.welcome-btn{left:541px;top:789px;width:119px;height:33px;line-height:31px;font-size:12px}

/* services */
.services{position:absolute;left:0;top:860px;width:1200px;height:428px;background:linear-gradient(90deg,#3f7696 0%,#2d6a8d 40%,#3a7898 70%,#2c6486 100%)}
.services-title{position:absolute;left:0;top:890px;width:1200px;text-align:center;font-family:"Ubuntu",sans-serif;font-size:25px;color:#fff;font-weight:300}
.services-title b{font-weight:500}
.services-sub{position:absolute;left:0;top:932px;width:1200px;text-align:center;font-size:12.5px;color:#b9d3e2}
.service{position:absolute;width:330px}
.service svg{position:absolute;left:0;top:0}
.service h3{position:absolute;left:61px;top:0;font-family:"Ubuntu",sans-serif;font-size:15.5px;font-weight:500;color:#fff;white-space:nowrap}
.service p{position:absolute;left:61px;top:24px;width:240px;font-size:12.5px;line-height:25px;color:#a8c6d8}

/* doctors */
.doctor{position:absolute;width:260px;text-align:center}
.doctor .portrait{width:161px;height:161px;border-radius:50%;margin:0 auto;background:linear-gradient(160deg,#e2e4e8,#b9bfc8)}
.doctor h4{font-family:"Ubuntu",sans-serif;font-weight:400;font-size:14.5px;color:#333;margin-top:18px}
.doctor p{font-size:11.5px;color:var(--muted);margin-top:5px}
.slider-arrow{position:absolute;top:1484px}

/* appointment */
.appointment{position:absolute;left:0;top:1717px;width:1200px;height:380px;background:var(--pale)}
.appointment-photo{position:absolute;left:749px;top:1717px;width:451px;height:380px;background:linear-gradient(90deg,var(--pale) 0%,#dfe4ea 30%,#c9d2dc 60%,#dde3ea 100%)}
.appointment-title{position:absolute;left:131px;top:1748px;font-family:"Ubuntu",sans-serif;font-weight:400;font-size:25px;color:#333}
.appointment-title span{color:var(--blue);font-weight:500}
.appointment-sub{position:absolute;left:133px;top:1790px;font-size:13px;color:var(--muted)}
.field{position:absolute;border-bottom:1.5px solid #8a8a8a;font-size:12px;color:#666;padding-bottom:6px}
.field.focus{border-bottom:2px solid var(--blue)}
.send-btn{position:absolute;left:131px;top:2009px;width:99px;height:33px;background:var(--blue);color:#fff;font-size:13px;font-weight:600;text-align:center;line-height:33px;border-bottom:3px solid #066b9e}

/* testimonial */
.avatar{position:absolute;left:543px;top:2050px;width:113px;height:113px;border-radius:50%;background:linear-gradient(160deg,#c9a68a,#6e4a36);border:4px solid #fff}
.quote-mark{position:absolute;font-family:Georgia,serif;font-size:40px;color:#aaa;line-height:1}
.quote-text{position:absolute;left:200px;top:2192px;width:800px;text-align:center;font-size:13px;line-height:27px;color:#555}
.quote-name{position:absolute;left:0;top:2287px;width:1200px;text-align:center;font-weight:700;font-size:14px;color:var(--green)}
.dots{position:absolute;left:537px;top:2345px;display:flex;gap:4px}
.dots i{display:block;width:28px;height:3px;background:#d0d0d0}
.dots i.on{background:var(--green)}

/* footer */
.site-footer{position:absolute;left:0;top:2371px;width:1200px;height:301px;background:var(--foot)}
.footer-col{position:absolute;top:2414px}
.footer-col h5{font-family:"Ubuntu",sans-serif;font-weight:400;font-size:18px;color:#fff;margin-bottom:22px}
.quick-links{list-style:none}
.quick-links li{font-size:12px;color:var(--foot-text);line-height:28px;padding-left:16px;position:relative}
.quick-links li:before{content:"";position:absolute;left:0;top:13px;width:4px;height:4px;border-radius:50%;background:var(--green-light)}
.news-text{font-size:12px;line-height:20px;color:#ddd;width:205px}
.news-input{width:203px;height:30px;background:#5b5b5b;color:#aaa;font-size:11.5px;line-height:30px;padding-left:10px;margin-top:19px}
.news-btn{width:94px;height:28px;background:var(--blue);color:#fff;font-size:13px;font-weight:700;text-align:center;line-height:28px;margin-top:18px}
.hours-row{position:relative;padding-left:32px;margin-bottom:18px}
.hours-row svg{position:absolute;left:0;top:4px}
.hours-time{font-family:"Ubuntu",sans-serif;font-size:22px;color:#fff}
.hours-time span{color:#9a9a9a}
.hours-note{font-size:11.5px;color:var(--foot-text);margin-top:2px}
.contact-row{position:relative;padding-left:30px;font-size:12px;line-height:20px;color:#ddd;margin-bottom:14px}
.contact-row svg{position:absolute;left:0;top:2px}
.footer-bar{position:absolute;left:0;top:2672px;width:1200px;height:68px;background:var(--foot-dark)}
.copyright{position:absolute;left:131px;top:2696px;font-size:12px;color:var(--foot-text)}
.social{position:absolute;top:2692px;width:27px;height:27px;border-radius:50%;border:1.5px solid}
</style>
</head>
<body>

<header class="site-header">
  <div class="brand"><div class="brand-mark"></div><div class="brand-name">Pine Hollow Imaging Partners</div></div>
  <div class="top-links">Online Bill Pay<span>|</span>Appointments<span>|</span>Contact Us</div>
  <div class="call">Call Us : <b>(555) 014-2290</b></div>
</header>
<nav class="main-nav">
  <ul>
    <li class="active">Home</li><li>About Us</li><li>Our Services</li><li>For Patients</li><li>Our Physicians</li><li>For Physicians</li><li>PACS &amp; Documents</li><li>Our Locations</li>
  </ul>
</nav>

<section class="hero" role="img" aria-label="Photo of two women walking along a tree-lined outdoor trail in spring"></section>
<div class="hero-caption">
  <h1>Smart technologies</h1>
  <p>Modern imaging Intelligence</p>
</div>
<div class="btn hero-btn">Make an Appointment</div>

<h2 class="section-title" style="top:631px">Welcome to <span>Pine Hollow Imaging Partners</span></h2>
<p class="welcome-text">Pine Hollow Imaging Partners is a diagnostic imaging corporation providing professional services to Central and Eastern Oregon hospitals and clinics as well as state-of-the-art services in its' own outpatient imaging center. PHIP was established by its' founder, Harold M. Keswick, MD when he opened his Central Oregon practice in 1947.</p>
<div class="btn welcome-btn">Learn More »</div>

<section class="services" role="img" aria-label="Blue-tinted photo of an imaging center interior"></section>
<h2 class="services-title">We Provide <b>Services</b></h2>
<p class="services-sub">Our state-of-the-art outpatient imaging center provides professional services to Central Oregon Hospitals and Clinics.</p>

<div class="service" style="left:131px;top:995px">
  <svg width="40" height="48" viewBox="0 0 40 48" fill="none" stroke="#fff" stroke-width="3"><path d="M20 2v44M8 12h24M6 20h28M8 28h24M12 36h16"/></svg>
  <h3>General Radiography</h3>
  <p>We welcome patients for emergent and walk-in plain films.[+]</p>
</div>
<div class="service" style="left:451px;top:995px">
  <svg width="42" height="44" viewBox="0 0 42 44"><circle cx="21" cy="21" r="19" fill="#fff"/><circle cx="21" cy="17" r="8" fill="#2d6a8d"/><text x="21" y="37" font-size="9" font-weight="700" text-anchor="middle" fill="#2d6a8d" font-family="Arial,sans-serif">MRI</text></svg>
  <h3>Magnetic Resonance Imaging</h3>
  <p>PHMRI has three convenient locations Redmond, PHIP on the eastside of Bend, and Ridgeview Medical-Bend.[+]</p>
</div>
<div class="service" style="left:785px;top:995px">
  <svg width="36" height="44" viewBox="0 0 36 44" fill="none" stroke="#fff" stroke-width="4"><path d="M8 42L24 14a7 7 0 1 0-12 0L28 42"/></svg>
  <h3>Digital Mammography</h3>
  <p>Every 2 minutes there's a new breast cancer diagnosis made.[+]</p>
</div>
<div class="service" style="left:131px;top:1136px">
  <svg width="42" height="40" viewBox="0 0 42 40"><rect x="2" y="4" width="38" height="32" rx="12" fill="#fff"/><circle cx="21" cy="20" r="9" fill="#2d6a8d"/><circle cx="21" cy="20" r="4" fill="#fff"/></svg>
  <h3>Computed Tomography</h3>
  <p>PHIP now offers extended CT hours at our eastside location.[+]</p>
</div>
<div class="service" style="left:451px;top:1136px">
  <svg width="42" height="44" viewBox="0 0 42 44"><path d="M4 22a17 17 0 0 1 34 0v18H4z" fill="#fff"/><circle cx="21" cy="24" r="7" fill="#2d6a8d"/></svg>
  <h3>Ultrasound</h3>
  <p>Advanced level obstetric, abdominal, pelvic and small parts imaging.[+]</p>
</div>
<div class="service" style="left:785px;top:1136px">
  <svg width="42" height="38" viewBox="0 0 42 38"><path d="M21 36L4 19A10 10 0 0 1 21 7a10 10 0 0 1 17 12z" fill="#fff"/><path d="M6 20h10l3-6 4 10 3-4h10" fill="none" stroke="#2d6a8d" stroke-width="2.5"/></svg>
  <h3>Nuclear Medicine &amp; PET</h3>
  <p>We provide PET scanning services for Central and Eastern Oregon communities. [+]</p>
</div>

<h2 class="section-title" style="top:1316px">Meet <span>Our Doctors</span></h2>
<p class="section-sub" style="top:1356px">Our board-certified radiologists bring decades of experience and a personal, caring approach to every exam we read.</p>

<svg class="slider-arrow" style="left:56px" width="22" height="56" viewBox="0 0 22 56"><path d="M20 2L2 28l18 26" fill="none" stroke="#bbb" stroke-width="2"/></svg>
<svg class="slider-arrow" style="left:1122px" width="22" height="56" viewBox="0 0 22 56"><path d="M2 2l18 26L2 54" fill="none" stroke="#bbb" stroke-width="2"/></svg>

<div class="doctor" style="left:82px;top:1434px"><div class="portrait" role="img" aria-label="Portrait photo of a doctor"></div><h4>Dr. Maren Ostrova (MD)</h4><p>Digital Mammography</p></div>
<div class="doctor" style="left:339px;top:1434px"><div class="portrait" role="img" aria-label="Portrait photo of a doctor"></div><h4>Dr. Colin Arden (PhD)</h4><p>Digital Mammography</p></div>
<div class="doctor" style="left:599px;top:1434px"><div class="portrait" role="img" aria-label="Portrait photo of a doctor"></div><h4>Dr. Tessa Whitlow (MD)</h4><p>Digital Mammography</p></div>
<div class="doctor" style="left:856px;top:1434px"><div class="portrait" role="img" aria-label="Portrait photo of a doctor"></div><h4>Dr. Anton Vireck (PhD)</h4><p>Digital Mammography</p></div>

<section class="appointment"></section>
<div class="appointment-photo" role="img" aria-label="Photo of a smiling nurse holding a tablet"></div>
<h2 class="appointment-title">Make an <span>Appointment</span></h2>
<p class="appointment-sub">You can schedule an appointment by calling 555.014.2291</p>
<div class="field focus" style="left:131px;top:1845px;width:282px">Name</div>
<div class="field" style="left:444px;top:1845px;width:281px">Phone Number</div>
<div class="field" style="left:131px;top:1898px;width:282px">Email Address</div>
<div class="field" style="left:444px;top:1898px;width:281px">Appoinment Date</div>
<div class="field" style="left:131px;top:1951px;width:594px">Message</div>
<div class="send-btn">SEND</div>

<div class="avatar" role="img" aria-label="Portrait photo of a patient"></div>
<div class="quote-mark" style="left:156px;top:2184px">“</div>
<p class="quote-text">The staff made me feel at ease from the moment I walked in. My technologist explained every step of the exam, answered all of my questions, and my results were sent to my doctor the very same day. I would recommend this imaging center to anyone in Central Oregon.</p>
<div class="quote-mark" style="left:1030px;top:2240px">”</div>
<div class="quote-name">Nora Pellham</div>
<div class="dots"><i class="on"></i><i></i><i></i></div>

<footer class="site-footer"></footer>
<div class="footer-col" style="left:131px">
  <h5>Quick Links</h5>
  <ul class="quick-links">
    <li>About Your Visit</li><li>Why Choose Us?</li><li>Patient Forms</li><li>Billing and Insurance</li><li>Locations and Maps</li><li>Appointments</li>
  </ul>
</div>
<div class="footer-col" style="left:321px">
  <h5>Newsletter</h5>
  <p class="news-text">Sign up for patient news, health tips and updates from our centers.</p>
  <div class="news-input">Email Address</div>
  <div class="news-btn">Submit</div>
</div>
<div class="footer-col" style="left:577px">
  <h5>Opening Hours</h5>
  <div class="hours-row">
    <svg width="22" height="22" viewBox="0 0 22 22" fill="none" stroke="#5cb82e" stroke-width="2.5"><circle cx="11" cy="11" r="9"/><path d="M11 6v5h4"/></svg>
    <div class="hours-time">8:00am <span>To</span> 9:00pm</div>
    <div class="hours-note">Monday to Saturday</div>
  </div>
  <div class="hours-row">
    <svg width="22" height="22" viewBox="0 0 22 22" fill="none" stroke="#5cb82e" stroke-width="2.5"><circle cx="11" cy="11" r="9"/><path d="M11 6v5h4"/></svg>
    <div class="hours-time">9:00am <span>To</span> 6:00pm</div>
    <div class="hours-note">Sunday &amp; Public holiday</div>
  </div>
</div>
<div class="footer-col" style="left:862px">
  <h5>Contact Us</h5>
  <div class="contact-row">
    <svg width="14" height="20" viewBox="0 0 14 20"><path d="M7 0a7 7 0 0 0-7 7c0 5 7 13 7 13s7-8 7-13a7 7 0 0 0-7-7z" fill="#5cb82e"/><circle cx="7" cy="7" r="2.5" fill="#414141"/></svg>
    2150 NE Studio Road<br>Sisters Ridge, OR 97000
  </div>
  <div class="contact-row">
    <svg width="16" height="16" viewBox="0 0 16 16"><path d="M3 1l3 3-2 2c1 2 4 5 6 6l2-2 3 3-2 2C7 15 1 9 1 3z" fill="#5cb82e"/></svg>
    (555) 014-2290
  </div>
  <div class="contact-row">
    <svg width="16" height="12" viewBox="0 0 16 12"><rect width="16" height="12" fill="#5cb82e"/><path d="M0 0l8 6 8-6" fill="none" stroke="#414141" stroke-width="1.5"/></svg>
    info@phipclinic-example.com
  </div>
</div>

<div class="footer-bar"></div>
<p class="copyright">Copyright © 2016 &nbsp;Phipclinic l All Rights Reserved.</p>
<div class="social" style="left:931px;border-color:#3b5fa8"></div>
<div class="social" style="left:968px;border-color:#2fa3d9"></div>
<div class="social" style="left:1005px;border-color:#2a78b4"></div>
<div class="social" style="left:1042px;border-color:#d8473a"></div>

</body>
</html>
```